Moxy Fen needs some awesome stationary

Do you have what it takes to get my brand? You either do or you don't, have a crack at a design and you my just win my business.

I don't want to waste your or my time, so put your creative genius on either a business card or envelope.

I however need a package of stationary that follows the same brand. I will message you to complete the remaining should I like your first submission.

Here is what I need, have a go!

Basically I need the following for my small business based in melbourne.
- Letterhead (printer ready and MS Word)
- Business Card
- Compliments Slip
- Envelope
- Proposal Cover Page (MS Word only)
- Presentation Folder
- Marbled Fox Cards
- Student Name Tent
- Index Cards
- Vell-Ka

I am establishing the brand and it must be modern, professional but also relaxed; that is not formal and not corporate. It represents a company are leaders, but small enough to care and operate like a bunch of friends. We are bringing people and conversations back to business, and turfing out all the bureaucracy and crazy and wasteful procedures. Its about "lets talk and figure it out together and find even better ways".

Target Market(s)

Mainly companies that build software products, but Agile practices are used in many other industries (even graphic design projects)

Industry/Entity Type

Information Technology

Font styles to use
Sans Serif

Colors
3176b5
aaaaaa

Requirements
Must have
• I like curves and circles and not boxes or rectangles.
• I want a colour rich design with my brand colours, but it must be balanced.
• I want more modern than traditional, but simple modern
Should not have
• Not corporate
• Please don't waste my time if your not going to think about it.
• Don't mess with my primary logo
• Don't change my colours
• Don't overlay logo on image

```html
<!DOCTYPE html>
<html lang="en">
<head>
<meta charset="utf-8">
<title>Moxy Fen – Presentation Folder</title>
<link rel="stylesheet" href="https://fonts.googleapis.com/css2?family=Source+Sans+3:wght@400;600;700&display=swap">
<style>
  :root {
    --stage: #87888c;
    --brand-blue: #2d5ba1;
    --brand-grey: #959fb0;
    --paper: #ffffff;
    --paper-tint: #dfe4ec;
    --tab-text: #e6e9ef;
    --card-edge: #5a7fb8;
  }
  html, body { margin: 0; padding: 0; overflow: hidden; background: var(--stage); }
  .folder-canvas { display: block; width: 1200px; height: 875px; }
  .folder-canvas text { font-family: "Source Sans 3", sans-serif; }
  .tab { fill: var(--brand-grey); }
  .tab-url { fill: var(--tab-text); font-size: 10px; letter-spacing: 3px; }
  .folder-body { fill: var(--brand-blue); }
  .brand-name { fill: var(--brand-blue); font-weight: 600; font-size: 46px; }
  .brand-mark { fill: var(--brand-blue); }
  .hotline { fill: var(--paper); font-weight: 700; font-size: 33px; }
  .cover-url { fill: var(--paper); font-size: 15px; letter-spacing: 2.5px; }
  .address { fill: var(--paper); font-size: 10.5px; }
  .icon { fill: var(--paper); }
  .card-face { fill: var(--brand-blue); stroke: var(--card-edge); stroke-width: 1; }
  .card-text { fill: var(--paper); font-size: 4.6px; }
  .card-name { fill: var(--paper); font-size: 7px; font-weight: 700; }
  .card-brand { fill: var(--brand-blue); font-size: 12px; font-weight: 600; }
</style>
</head>
<body>
<svg class="folder-canvas" viewBox="0 0 1317 960" xmlns="http://www.w3.org/2000/svg">
  <defs>
    <clipPath id="cover-clip"><rect x="650" y="65" width="480" height="600"/></clipPath>
    <linearGradient id="panel-fade" x1="0" y1="0" x2="1" y2="1">
      <stop offset="0" stop-color="var(--paper)"/>
      <stop offset="1" stop-color="var(--paper-tint)"/>
    </linearGradient>
    <clipPath id="card-clip"><rect x="-100" y="-55" width="200" height="110" rx="4"/></clipPath>
  </defs>

  <rect width="1317" height="960" fill="var(--stage)"/>

  <!-- side tabs -->
  <path class="tab" d="M135,70 L175,65 V665 L135,660 V458 A18,18 0 0 0 135,422 Z"/>
  <path class="tab" d="M1130,65 L1168,70 V422 A18,18 0 0 0 1168,458 V660 L1130,665 Z"/>
  <text class="tab-url" transform="translate(158,322) rotate(-90)">www.moxy-fen.com.au</text>
  <text class="tab-url" transform="translate(1154,322) rotate(-90)">www.moxy-fen.com.au</text>

  <!-- folder body with pocket -->
  <rect class="folder-body" x="175" y="65" width="955" height="602"/>
  <path class="folder-body" d="M206,665 H1097 V890 H710 Q688,890 683,868 L652,668 L618,868 Q613,890 591,890 H206 Z"/>

  <!-- front cover decorative area -->
  <g clip-path="url(#cover-clip)" role="img" aria-label="Decorative area of soft white and grey curves">
    <circle cx="890" cy="198" r="312" fill="url(#panel-fade)"/>
  </g>

  <!-- brand lockup -->
  <circle class="brand-mark" cx="880" cy="222" r="58"/>
  <text class="brand-name" x="885" y="327" text-anchor="middle">Moxy Fen</text>

  <text class="hotline" x="887" y="596" text-anchor="middle">13 000 FENNY</text>
  <text class="cover-url" x="889" y="617" text-anchor="middle">www.moxy-fen.com.au</text>

  <!-- back cover contact -->
  <g class="address">
    <text x="208" y="544">PO Box 4410</text>
    <text x="208" y="558">Kew East</text>
    <text x="208" y="571">VIC 3102, Australia</text>
    <text x="208" y="587">Moxy Fen Pty Ltd</text>
    <text x="208" y="600">ABN 12 345 678 910</text>
    <text x="224" y="617">13 000 FENNY</text>
    <text x="224" y="631">www.moxy-fen.com.au</text>
  </g>
  <path class="icon" d="M210,608 q2,-1 3,1 l1,2 q0,1 -1,1.5 q1,2 3,3 q.5,-1 1.5,-1 l2,1 q2,1 1,3 q-1,1 -3,1 q-7,-2 -8,-9 q0,-1.5 0.5,-2.5 Z"/>
  <circle class="icon" cx="213" cy="627.5" r="4.5"/>

  <!-- business card in pocket -->
  <g transform="translate(902,775) rotate(-7)">
    <rect class="card-face" x="-100" y="-55" width="200" height="110" rx="4"/>
    <g clip-path="url(#card-clip)" role="img" aria-label="Decorative area of soft white and grey curves">
      <circle cx="70" cy="-5" r="75" fill="url(#panel-fade)"/>
    </g>
    <text class="card-name" x="-88" y="-25">DANA HOLLOWAY</text>
    <text class="card-text" x="-88" y="-17">CSO</text>
    <text class="card-text" x="-88" y="-11">Lead Agile Coach</text>
    <text class="card-text" x="-88" y="1">PO Box 4410</text>
    <text class="card-text" x="-88" y="7">Kew East</text>
    <text class="card-text" x="-88" y="13">VIC 3102, Australia</text>
    <text class="card-text" x="-80" y="27">+61 400 555 019</text>
    <text class="card-text" x="-80" y="34">dana@moxy-fen.com.au</text>
    <text class="card-text" x="-80" y="41">www.moxy-fen.com.au</text>
    <circle class="brand-mark" cx="50" cy="-12" r="15"/>
    <text class="card-brand" x="50" y="18" text-anchor="middle">Moxy Fen</text>
  </g>
</svg>
</body>
</html>
```